landscaping core flute signs

I need core flutes created with business name and a few extra dot points for putting on fences for job sites 120cm x 120cm approx.
I want our old ones information with the new L logo and colour palette

```html
<!DOCTYPE html>
<html lang="en">
<head>
<meta charset="utf-8">
<title>Grounded Form – Site Sign</title>
<link href="https://fonts.googleapis.com/css2?family=Bebas+Neue&family=Montserrat:wght@500;600;700;800&display=swap" rel="stylesheet">
<style>
  :root{
    --backdrop:#4a4a4a;
    --green:#648f5a;
    --green-dark:#4b7340;
    --ink:#040406;
    --white:#ffffff;
    --panel-top:#d4d4d4;
    --panel-mid:#ffffff;
    --panel-low:#d2cfd0;
  }
  html,body{margin:0;padding:0;overflow:hidden;}
  body{width:1190px;height:1200px;background:var(--backdrop);position:relative;}
  .sign{
    position:absolute;left:180px;top:179px;width:832px;height:832px;overflow:hidden;
    background:linear-gradient(to bottom,var(--panel-top) 0%,var(--panel-mid) 32%,var(--panel-mid) 55%,var(--panel-low) 80%);
  }
  .licence{
    position:absolute;left:36px;top:40px;height:21px;display:flex;border-radius:11px;overflow:hidden;
    font-family:"Montserrat",sans-serif;font-weight:600;font-size:15px;line-height:21px;letter-spacing:1px;
  }
  .licence .label{background:var(--ink);color:var(--white);padding:0 4px 0 8px;}
  .licence .number{background:var(--green);color:var(--white);padding:0 8px 0 6px;border-radius:11px 0 0 11px;margin-left:-6px;}
  .brand-mark{
    position:absolute;left:312px;top:34px;width:208px;height:208px;border-radius:50%;background:var(--green);
  }
  .brand-name{
    position:absolute;left:0;right:0;top:268px;margin:0;text-align:center;
    font-family:"Montserrat",sans-serif;font-weight:700;font-size:54px;line-height:58px;color:var(--ink);letter-spacing:2px;
  }
  .services{
    position:absolute;left:0;right:0;margin:0;text-align:center;
    font-family:"Bebas Neue",sans-serif;font-size:50px;line-height:50px;color:var(--green);
  }
  .services.primary{top:420px;}
  .services.primary .divider{display:inline-block;width:4px;height:50px;background:var(--ink);vertical-align:top;margin:2px 26px 0;}
  .services.secondary{top:497px;}
  .chevron{position:absolute;left:0;top:0;width:832px;height:832px;}
  .phone{
    position:absolute;left:0;right:0;top:664px;margin:0;text-align:center;
    font-family:"Montserrat",sans-serif;font-weight:800;font-size:84px;line-height:90px;color:var(--white);letter-spacing:1px;
  }
  .email{
    position:absolute;left:0;right:0;top:760px;margin:0;display:flex;justify-content:center;align-items:center;gap:8px;
    font-family:"Montserrat",sans-serif;font-weight:500;font-size:31px;line-height:34px;color:var(--green);letter-spacing:3px;
  }
  .email svg{width:30px;height:28px;}
</style>
</head>
<body>
  <main class="sign">
    <div class="licence"><span class="label">QBSA</span><span class="number">1234567</span></div>

    <div class="brand-mark" aria-hidden="true"></div>
    <h1 class="brand-name">GROUNDED<br>FORM</h1>

    <p class="services primary">Paving &amp; Concreting<span class="divider"></span>Fencing &amp; Retaining</p>
    <p class="services secondary">Design &amp; Construct</p>

    <svg class="chevron" viewBox="0 0 832 832" aria-hidden="true">
      <polygon points="0,502 415,617 832,502 832,539 415,651 0,539" fill="var(--green)"/>
      <polygon points="415,617 832,502 832,539 475,633" fill="var(--green-dark)"/>
      <polygon points="0,539 415,651 832,539 832,832 0,832" fill="var(--ink)"/>
    </svg>

    <p class="phone">0412 555 019</p>
    <p class="email">
      <svg viewBox="0 0 30 28" aria-hidden="true">
        <rect x="2" y="9" width="26" height="17" fill="none" stroke="var(--green)" stroke-width="2.4"/>
        <polyline points="2,10 15,19 28,10" fill="none" stroke="var(--green)" stroke-width="2.4"/>
        <rect x="8" y="2" width="14" height="11" fill="none" stroke="var(--green)" stroke-width="2"/>
      </svg>
      sam@groundedform.com
    </p>
  </main>
</body>
</html>
```